Lunelle Rosa Hair Fancy Business Card’s

I want my business cards to be elite, original and very classy. I want the business cards to match the colors of my logo and to match the design posted. I would love the design of the picture I posted

I want the card all white .
The dripping on the top of the card I want it to match the pink color in my logo that’s also posted .
I need my logo on the business card !
I need my Instagram- @lunelle.rosa.hair__
And my phone number - 555 207 3962

Target Market(s)

My target market is young woman age 23 to older woman to the age of 65
I want both older and younger women to love my design . I don’t want any cheap looking business cards

Industry/Entity Type

Hair And Beauty

Contact Information for Business Card

Add my logo
Add my Instagram- @lunelle.rosa.hair__
My number - 555 207 3962
My website- www.lunellerosahair.example

Font styles to use
Serif
Script

Colors
ffffff
e667a6
e34298

Requirements
Must have
• The business cards must have my logo, my number , my website, and my Instagram!
Nice to have
• Nice to have glitter words that match my logo
• The business cards must look classy and mature
• I want them to be very unique!!
Should not have
• Should not have any colors that doesn’t match my logo ! This is very important! Please

```html
<!DOCTYPE html>
<html lang="en">
<head>
<meta charset="utf-8">
<title>Lunelle Rosa Hair – Business Card</title>
<link rel="stylesheet" href="https://fonts.googleapis.com/css2?family=Roboto+Slab:wght@600&family=Montserrat:wght@400;500&display=swap">
<style>
  :root {
    --stage: #dcdcde;
    --card: #ffffff;
    --pink: #e34298;
    --pink-soft: #e667a6;
    --white: #ffffff;
  }
  * { margin: 0; padding: 0; box-sizing: border-box; }
  html, body { width: 1200px; height: 800px; overflow: hidden; }
  body {
    background: var(--stage);
    display: flex;
    align-items: center;
    justify-content: center;
    gap: 40px;
  }
  .card {
    position: relative;
    width: 525px;
    height: 300px;
    background: var(--card);
    box-shadow: 0 10px 24px rgba(0,0,0,0.16);
    overflow: hidden;
  }
  .drip {
    position: absolute;
    top: 0; left: 0;
    width: 525px;
    height: 92px;
    display: block;
  }
  .drip path { fill: var(--pink); }

  /* contact side */
  .info-band {
    position: absolute;
    left: 0; right: 0;
    top: 118px;
    height: 124px;
    background: var(--pink);
    border-top: 7px solid var(--pink-soft);
    border-bottom: 7px solid var(--pink-soft);
    display: flex;
    align-items: center;
    justify-content: space-between;
    padding: 0 36px 0 70px;
  }
  .holder { text-align: right; color: var(--white); font-family: "Roboto Slab", serif; font-weight: 600; }
  .holder-name { font-size: 25px; line-height: 1.1; white-space: nowrap; }
  .holder-role { font-size: 16px; margin-top: 3px; }
  .contact-list { list-style: none; font-family: "Montserrat", sans-serif; font-size: 12.5px; color: var(--white); }
  .contact-list li { display: flex; align-items: center; gap: 9px; line-height: 20px; white-space: nowrap; }
  .contact-list svg { width: 11px; height: 11px; flex: none; }

  /* name side */
  .card-front { border: 6px solid var(--pink-soft); }
  .brand {
    position: absolute;
    left: 0; right: 0;
    top: 150px;
    display: flex;
    align-items: center;
    justify-content: center;
    gap: 12px;
  }
  .brand-dot { width: 12px; height: 12px; border-radius: 50%; background: var(--pink); }
  .brand-name {
    font-family: "Montserrat", sans-serif;
    font-weight: 500;
    font-size: 30px;
    letter-spacing: 0.06em;
    color: var(--pink);
  }
</style>
</head>
<body>
  <section class="card card-back">
    <svg class="drip" viewBox="0 0 525 92" aria-hidden="true">
      <path d="M0,0 H525 V24 Q515,30 506,26 V44 a6,6 0 0 1 -12,0 V28 Q470,32 446,26 V70 a7,7 0 0 1 -14,0 V30 Q390,34 346,26 V58 a6,6 0 0 1 -12,0 V30 Q300,32 256,26 V82 a7,7 0 0 1 -14,0 V30 Q200,34 156,26 V50 a6,6 0 0 1 -12,0 V28 Q100,32 66,26 V66 a6,6 0 0 1 -12,0 V30 Q20,34 0,26 Z"/>
    </svg>
    <div class="info-band">
      <div class="holder">
        <p class="holder-name">Daniel Harper</p>
        <p class="holder-role">President</p>
      </div>
      <ul class="contact-list">
        <li>
          <svg viewBox="0 0 12 12"><path d="M2.5 1 L4.5 1 L5.2 3.6 L4 4.6 Q5 7 7.4 8 L8.4 6.8 L11 7.5 L11 9.5 Q10.5 11 9 11 Q1 10 1 3 Q1 1.5 2.5 1 Z" fill="#fff"/></svg>
          555 207 3962
        </li>
        <li>
          <svg viewBox="0 0 12 12"><circle cx="6" cy="6" r="5" fill="#fff"/></svg>
          @lunelle.rosa.hair__
        </li>
        <li>
          <svg viewBox="0 0 12 12"><rect x="0.5" y="2" width="11" height="8" fill="#fff"/><path d="M0.5 2 L6 6.5 L11.5 2" fill="none" stroke="#e34298" stroke-width="1"/></svg>
          info@lunellerosahair.example
        </li>
        <li>
          <svg viewBox="0 0 12 12"><circle cx="6" cy="6" r="5" fill="#fff"/></svg>
          www.lunellerosahair.example
        </li>
      </ul>
    </div>
  </section>

  <section class="card card-front">
    <svg class="drip" viewBox="0 0 525 92" aria-hidden="true">
      <path d="M0,0 H525 V24 Q515,30 506,26 V44 a6,6 0 0 1 -12,0 V28 Q470,32 446,26 V70 a7,7 0 0 1 -14,0 V30 Q390,34 346,26 V58 a6,6 0 0 1 -12,0 V30 Q300,32 256,26 V82 a7,7 0 0 1 -14,0 V30 Q200,34 156,26 V50 a6,6 0 0 1 -12,0 V28 Q100,32 66,26 V66 a6,6 0 0 1 -12,0 V30 Q20,34 0,26 Z"/>
    </svg>
    <div class="brand">
      <span class="brand-dot"></span>
      <span class="brand-name">Lunelle Rosa Hair</span>
    </div>
  </section>
</body>
</html>
```